The Plate Compass

Cutting Through the Noise to What Actually Works.

Nutrition book

Target Market(s)

People looking to be or get healthy and eat right.

```html
<!DOCTYPE html>
<html lang="en">
<head>
<meta charset="utf-8">
<title>The Plate Compass – Book Cover</title>
<link rel="stylesheet" href="https://fonts.googleapis.com/css2?family=Poppins:wght@800;900&family=Montserrat:wght@500;600&display=swap">
<style>
  :root {
    --stage: #efe9df;
    --cover-yellow: #fdb71a;
    --title-white: #ffffff;
    --ink: #1b1712;
    --photo-dark: #1f1a17;
    --photo-warm: #5a2c16;
    --photo-red: #8a3a1c;
    --photo-green: #3f5a24;
  }
  * { box-sizing: border-box; margin: 0; padding: 0; }
  html, body {
    width: 1200px;
    height: 1200px;
    overflow: hidden;
    background: var(--stage);
  }
  .canvas {
    position: relative;
    width: 1200px;
    height: 1200px;
    display: flex;
    align-items: center;
    justify-content: center;
  }
  .cover {
    position: relative;
    width: 870px;
    height: 1160px;
    background: var(--cover-yellow);
    overflow: hidden;
    box-shadow: 0 10px 30px rgba(0,0,0,0.12);
  }
  .cover-photo {
    position: absolute;
    left: 150px;
    top: 250px;
    width: 670px;
    height: 680px;
    border-radius: 44px;
    background:
      radial-gradient(circle at 70% 30%, var(--photo-warm) 0%, transparent 40%),
      radial-gradient(circle at 30% 75%, var(--photo-red) 0%, transparent 38%),
      radial-gradient(circle at 85% 55%, var(--photo-green) 0%, transparent 25%),
      var(--photo-dark);
  }
  .title {
    position: absolute;
    left: 60px;
    top: 80px;
    font-family: "Poppins", sans-serif;
    font-weight: 900;
    font-size: 128px;
    line-height: 0.9;
    letter-spacing: -4px;
    color: var(--title-white);
  }
  .title-line {
    display: block;
    width: fit-content;
    background: var(--cover-yellow);
    padding: 4px 22px 10px 10px;
    border-radius: 0 0 34px 0;
  }
  .subtitle {
    position: absolute;
    left: 410px;
    top: 530px;
    font-family: "Poppins", sans-serif;
    font-weight: 800;
    line-height: 0.92;
  }
  .subtitle-outline {
    display: block;
    font-size: 96px;
    letter-spacing: -2px;
    color: transparent;
    -webkit-text-stroke: 2.5px var(--title-white);
  }
  .subtitle-solid {
    display: block;
    font-size: 150px;
    letter-spacing: -4px;
    color: var(--ink);
    -webkit-text-stroke: 2px var(--title-white);
    margin-top: 4px;
  }
  .tagline {
    position: absolute;
    left: 0;
    right: 0;
    top: 985px;
    text-align: center;
    font-family: "Montserrat", sans-serif;
    font-weight: 600;
    font-size: 27px;
    letter-spacing: 10px;
    color: var(--ink);
  }
  .author {
    position: absolute;
    left: 0;
    right: 0;
    top: 1070px;
    text-align: center;
    font-family: "Montserrat", sans-serif;
    font-weight: 500;
    font-size: 22px;
    letter-spacing: 8px;
    color: var(--title-white);
  }
</style>
</head>
<body>
  <main class="canvas">
    <section class="cover">
      <div class="cover-photo" role="img" aria-label="Photo of an overhead spread of burgers, fries, chicken wings, onion rings, cherry tomatoes and lettuce on a dark table"></div>
      <h1 class="title">
        <span class="title-line">The</span>
        <span class="title-line">Plate</span>
        <span class="title-line">Compass</span>
      </h1>
      <h2 class="subtitle">
        <span class="subtitle-outline">Cutting</span>
        <span class="subtitle-outline">Through</span>
        <span class="subtitle-outline">the</span>
        <span class="subtitle-solid">Noise</span>
      </h2>
      <p class="tagline">TO WHAT ACTUALLY WORKS.</p>
      <p class="author">YOUR NAME HERE</p>
    </section>
  </main>
</body>
</html>
```